LB - WESITE NEEDED PAGE: Clean / Modern / Pro & Dynamic

Lantern-Brokers is a new insurance brokerage firm dealing exclusively with companies (BToB) providing the following property: Liabilities Insurance Insurances Automobile Insurance Insurances Construction% 26amp; Engineering Casualty Workmen 's Compensation Health Insurance Marime% 26amp; Transit Credit Insurance Young, Fast, Proactive and Dynamic we call ourselves Lantern-Brokers because we are a "start-up" willing to make a difference in the market, bringing modernity and speed to our industry, still too bureaucratic / procedural / opaque uninitiated. We need something respecting the colors of our orange logtype; blue; white; black; easy to scroll, with simple information on the company; - who we are - our team (with the pictures) - what we do - what we do - contact us, contact us (google map) Luanda (Angola) Small company, just need something flashy / professional / structured / modern.

Target Market(s)

BtoB; Oil and gas companies; French speaking copying established in Angola, all industrials, factories and importers of goods.

Industry/Entity Type

Insurance Broker

Font styles to use
Sans Serif

Colors

Designer to choose colors to be used in the design.

Requirements
Must have
• We need something respecting the colors of our orange logtype; blue; white; black; easy to scroll, with simple information on the company; - who we are - our team (with the pictures) - what we do - what we do - contact us, contact us (google map) Luanda (Angola) Small company, just need something flashy / professional / structured / modern.
Nice to have
• A page format
Should not have
• WE DO NOT WANT A REFER TO OUR LOGO, but a Home Page for our Website with the basics categories ... >> PLEASE CAREFULLY USE THE RIGHT COLOR OF THE LOGOTYPE which are the ones enclosed Orange / Turquoise / Black as per the business card .

```html
<!DOCTYPE html>
<html lang="en">
<head>
<meta charset="utf-8">
<title>Lantern Insurance Brokers</title>
<link href="https://fonts.googleapis.com/css2?family=Michroma&family=Montserrat:ital,wght@0,400;0,500;0,600;1,500&display=swap" rel="stylesheet">
<style>
:root{
  --orange:#f26522;
  --orange-light:#f7931e;
  --blue:#1e8fe8;
  --ink:#1d1d1f;
  --text:#4a4a4a;
  --muted:#9a9a9a;
  --line:#e3e3e3;
  --soft:#f5f5f5;
  --night:#0b0b0c;
  --white:#ffffff;
}
*{box-sizing:border-box;margin:0;padding:0}
html,body{width:1200px;height:3617px;overflow:hidden}
body{font-family:"Montserrat",sans-serif;color:var(--text);background:var(--white);position:relative}
.abs{position:absolute}
.display{font-family:"Michroma",sans-serif}

/* header */
.site-header{position:absolute;left:0;top:0;width:1200px;height:70px;background:rgba(30,36,44,.82);z-index:3}
.brand{position:absolute;left:146px;top:48px;font-weight:600;font-size:13px;color:var(--orange);letter-spacing:.2px;display:flex;align-items:center;gap:6px}
.brand-dot{width:38px;height:38px;border-radius:50%;background:var(--orange);position:absolute;left:40px;top:-42px}
.main-nav{position:absolute;left:324px;top:29px;display:flex;gap:32px;font-size:11.5px;font-weight:500;color:var(--white);letter-spacing:.3px}
.main-nav .active{color:var(--orange)}
.header-phone{position:absolute;left:936px;top:22px;display:flex;align-items:center;gap:10px;color:var(--white);font-size:12.5px;font-weight:500}
.ring{width:28px;height:28px;border-radius:50%;border:2px solid var(--orange);display:flex;align-items:center;justify-content:center}

/* hero */
.hero{position:absolute;left:0;top:0;width:1200px;height:618px;background:linear-gradient(180deg,#5b7591 0%,#3d5369 40%,#27313d 75%,#1e2630 100%)}
.hero h1{position:absolute;left:0;width:1200px;top:228px;text-align:center;color:var(--white);font-family:"Michroma",sans-serif;font-size:39px;line-height:52px;font-weight:400;text-shadow:0 2px 6px rgba(0,0,0,.4)}
.hero p{position:absolute;left:0;width:1200px;top:328px;text-align:center;color:var(--white);font-size:13px;font-weight:600;line-height:16px}
.btn{position:absolute;height:30px;border-radius:15px;background:linear-gradient(90deg,var(--orange-light),var(--orange));color:var(--white);font-size:11.5px;font-weight:500;display:flex;align-items:center;justify-content:center;letter-spacing:.3px}
.notch{position:absolute;left:570px;top:590px;width:60px;height:30px;background:var(--white);border-radius:30px 30px 0 0}
.mouse{position:absolute;left:592px;top:604px;width:14px;height:20px;border:1.6px solid var(--orange);border-radius:7px}

/* section titles */
.eyebrow{position:absolute;left:0;width:1200px;text-align:center;color:var(--blue);font-size:12.5px;font-weight:500}
.title{position:absolute;left:0;width:1200px;text-align:center;font-family:"Michroma",sans-serif;font-size:29px;color:var(--ink)}
.title-rule{position:absolute;left:570px;width:60px;height:1.5px;background:var(--blue)}
.lead{position:absolute;left:0;width:1200px;text-align:center;font-size:10px;color:var(--muted)}

/* about */
.about-photo{position:absolute;left:156px;top:808px;width:442px;height:297px;background:#fff;box-shadow:0 0 10px rgba(0,0,0,.18);padding:7px}
.about-photo div{width:100%;height:100%;background:linear-gradient(135deg,#c9d9e8,#8fa9c0 60%,#5a6f82)}
.about-heading{position:absolute;left:636px;top:810px;width:330px;font-size:16px;line-height:23px;font-weight:500;color:var(--orange)}
.about-text{position:absolute;left:636px;top:863px;width:420px;font-size:10px;line-height:19.2px;color:var(--muted);text-align:justify}
.about-rule{position:absolute;left:715px;top:1027px;width:1px;height:38px;background:var(--line)}

/* services */
.services{position:absolute;left:0;top:1173px;width:1200px;height:456px;background:var(--soft)}
.service{position:absolute;width:200px;text-align:center}
.service svg{display:block;margin:0 auto}
.service h3{font-size:12.5px;font-weight:500;color:var(--ink);line-height:17px;margin-top:12px}
.service.featured h3{color:var(--orange)}

/* testimonial */
.testimonial{position:absolute;left:0;top:1629px;width:1200px;height:442px;background:linear-gradient(120deg,#4a4c54 0%,#5f5c5f 45%,#6e665e 75%,#55524f 100%)}
.testimonial .eyebrow{color:var(--white)}
.testimonial .title,.testimonial .lead{color:var(--white)}
.avatar{position:absolute;left:563px;top:167px;width:74px;height:74px;border-radius:50%;border:3px solid #fff;background:linear-gradient(160deg,#9bb7d1,#4d6e8f)}
.client-name{position:absolute;left:655px;top:186px;color:var(--white);font-size:12px;font-weight:500}
.client-role{position:absolute;left:657px;top:206px;color:#ddd;font-size:9.5px;font-style:italic}
.quote{position:absolute;left:270px;top:252px;width:660px;text-align:center;color:var(--white);font-size:10.6px;line-height:18px}
.dots{position:absolute;left:583px;top:364px;display:flex;gap:8px}
.dots span{width:7px;height:7px;border-radius:50%;background:#fff}
.dots .on{background:var(--orange)}

/* team */
.member{position:absolute;top:2243px;width:214px;height:313px;background:#fff;box-shadow:0 0 6px rgba(0,0,0,.12);text-align:center}
.member .photo{height:180px;background:linear-gradient(180deg,#e4e7ea,#b9c0c8)}
.member h3{font-size:12.5px;font-weight:500;color:var(--ink);margin-top:20px}
.member .role{font-size:11.5px;font-style:italic;color:var(--orange);margin-top:4px;font-weight:500}
.member p{font-size:10px;line-height:17px;color:var(--muted);margin:8px 18px 0}
.social-strip{position:absolute;left:0;top:40px;width:22px;height:82px;background:#fff;border-radius:0 12px 12px 0;display:flex;flex-direction:column;align-items:center;justify-content:center;gap:11px}
.social-strip span{width:8px;height:8px;border-radius:50%;background:var(--ink)}

/* contact */
.contact{position:absolute;left:0;top:2620px;width:1200px;height:575px;background:#fafafa}
.field{position:absolute;height:42px;border:1px solid var(--line);background:#fff;font-size:10px;color:#555;padding:13px 11px}
.field.message{height:96px;padding-top:14px}

/* newsletter */
.newsletter{position:absolute;left:0;top:3195px;width:1200px;height:70px;background:linear-gradient(90deg,var(--orange),var(--orange-light) 60%,var(--orange))}
.nl-icon{position:absolute;left:152px;top:18px;width:34px;height:34px;border-radius:50%;border:2px solid #fff;background:var(--blue);display:flex;align-items:center;justify-content:center}
.nl-title{position:absolute;left:198px;top:20px;font-family:"Michroma",sans-serif;font-size:20px;color:#fff}
.nl-input{position:absolute;left:483px;top:20px;width:353px;height:31px;background:#fff;font-size:10px;color:#555;padding:10px 10px}
.nl-btn{position:absolute;left:860px;top:20px;width:122px;height:31px;border-radius:16px;background:var(--blue);color:#fff;font-size:12.5px;font-weight:500;display:flex;align-items:center;justify-content:center}

/* footer */
.site-footer{position:absolute;left:0;top:3265px;width:1200px;height:317px;background:var(--night)}
.foot-title{position:absolute;font-family:"Michroma",sans-serif;font-size:19px;color:#fff}
.foot-rule{position:absolute;height:1px;background:#333}
.quick-links{position:absolute;left:143px;top:84px;list-style:none;font-size:11px;color:#fff}
.quick-links li{height:30px;display:flex;align-items:center;gap:8px}
.quick-links li::before{content:"";width:4px;height:4px;border-radius:50%;background:#fff}
.quick-links .active{color:var(--orange)}
.quick-links .active::before{background:var(--orange)}
.vline{position:absolute;left:343px;top:40px;width:1px;height:235px;background:#2a2a2a}
.info{position:absolute;left:413px;display:flex;gap:12px;color:#fff;font-size:10px;line-height:16px}
.info .ico{width:24px;height:24px;background:var(--blue);border-radius:3px;display:flex;align-items:center;justify-content:center;flex:none}
.info strong{font-size:15px;font-weight:500;display:block;line-height:20px}
.social{position:absolute;left:413px;top:263px;display:flex;gap:7px}
.social span{width:22px;height:22px;border-radius:50%;border:2px solid #fff;background:var(--blue)}
.map{position:absolute;left:650px;top:0;width:550px;height:317px;background:linear-gradient(135deg,#eceff1,#dfe3e6);clip-path:polygon(0 0,100% 0,100% 100%,0 100%,0 220px,26px 158px,0 96px)}
.copyright{position:absolute;left:0;top:3582px;width:1200px;height:35px;text-align:center;font-size:11px;color:var(--ink);line-height:35px}
</style>
</head>
<body>

<section class="hero" role="img" aria-label="Dusk city skyline with a tall glass tower on the right">
  <h1>LANTERN INSURANCE<br>BROKERS</h1>
  <p>We Are A New Insurance Brokerage Firm Dealing Exclusively<br>With Companies.</p>
  <a class="btn" style="left:526px;top:379px;width:132px">CONTACT US</a>
  <div class="notch"></div>
  <div class="mouse"></div>
</section>

<header class="site-header">
  <div class="brand"><span class="brand-dot"></span>Lantern-Brokers</div>
  <nav class="main-nav">
    <span class="active">HOME</span><span>WHO WE ARE</span><span>WHAT WE DO</span><span>TESTIMONIAL</span><span>OUR TEAM</span><span>CONTACT US</span>
  </nav>
  <div class="header-phone">
    <span class="ring"><svg width="12" height="12" viewBox="0 0 24 24"><path fill="#f26522" d="M6.6 10.8a15 15 0 0 0 6.6 6.6l2.2-2.2c.3-.3.7-.4 1-.2 1.1.4 2.3.6 3.6.6.6 0 1 .4 1 1V20c0 .6-.4 1-1 1A17 17 0 0 1 3 4c0-.6.4-1 1-1h3.5c.6 0 1 .4 1 1 0 1.3.2 2.5.6 3.6.1.3 0 .7-.2 1z"/></svg></span>
    (123) 555 0148
  </div>
</header>

<!-- who we are -->
<div class="eyebrow" style="top:693px">About Us</div>
<h2 class="title" style="top:716px">Who We Are</h2>
<div class="title-rule" style="top:756px"></div>
<p class="lead" style="top:766px">Lorem ipsum dolor sit amet, consectetuer adipiscing elit, sed diam nonummy nibh euismod tincidunt ut laoreet dolore magna</p>
<div class="about-photo"><div role="img" aria-label="Smiling businesswoman at a desk signing a document with a client"></div></div>
<h3 class="about-heading">WELCOME TO LANTERN INSURANCE BROKERS</h3>
<p class="about-text">Lorem Ipsum Dolor Sit Amet, Consectetuer Adipiscing Elit, Sed Diam Nonummy Nibh Euismod Tincidunt Ut Laoreet Dolore Magna Aliquam Erat Volutpat. Ut Wisi Enim Ad Minim Veniam, Quis Nostrud Exerci Tation Ullamcorper Suscipit Lobortis Nisl Ut Aliquip Ex Ea Commodo Consequat. Duis Autem Vel Eum Iriure Dolor In Hendrerit In Vulputate Velit Esse Molestie Consequat, Vel Illum Dolore Eu Feugiat Nulla Facilisis At Vero Eros Et Accumsan Et Iusto Odio Dignissim Qui Blandit Praesent Luptatum Zzril Delenit Augue Duis Dolore Te Feugait Nulla Facilisi. Lorem Ipsum Dolor Sit Amet, Consectetuer Adipiscing Elit.</p>
<div class="about-rule"></div>
<a class="btn" style="left:648px;top:1068px;width:130px">CONTACT US</a>

<!-- what we do -->
<section class="services">
  <div class="eyebrow" style="top:67px">Services</div>
  <h2 class="title" style="top:90px">What We Do</h2>
  <div class="title-rule" style="top:130px"></div>
  <p class="lead" style="top:143px">Lorem ipsum dolor sit amet, consectetuer adipiscing elit, sed diam nonummy nibh euismod tincidunt ut laoreet dolore magna</p>

  <div class="service" style="left:109px;top:185px">
    <svg width="140" height="140" viewBox="0 0 140 140"><path d="M70 2a68 68 0 1 1-68 68" fill="none" stroke="#1e8fe8" stroke-width="5" transform="rotate(-200 70 70)"/><circle cx="70" cy="70" r="54" fill="#fff"/><g fill="none" stroke="#333" stroke-width="2"><path d="M70 45l14 5v11c0 10-6 16-14 19-8-3-14-9-14-19V50z"/><path d="M70 50v26M60 62h20"/><path d="M48 72l8 10v12M92 72l-8 10v12"/></g></svg>
    <h3>Liabilities<br>Insurance</h3>
  </div>
  <div class="service" style="left:304px;top:185px">
    <svg width="140" height="140" viewBox="0 0 140 140"><path d="M70 2a68 68 0 1 1-68 68" fill="none" stroke="#1e8fe8" stroke-width="5" transform="rotate(-200 70 70)"/><circle cx="70" cy="70" r="54" fill="#fff"/><g fill="none" stroke="#333" stroke-width="2"><circle cx="70" cy="70" r="26"/><path d="M52 76l4-10h26l4 10v8H52z"/><circle cx="60" cy="84" r="3"/><circle cx="80" cy="84" r="3"/><path d="M84 52l6-2v6c0 4-3 6-6 7-3-1-6-3-6-7v-6z"/></g></svg>
    <h3>Automobile<br>Insurance</h3>
  </div>
  <div class="service featured" style="left:499px;top:185px">
    <svg width="140" height="140" viewBox="0 0 140 140"><path d="M70 2a68 68 0 1 1-68 68" fill="none" stroke="#f26522" stroke-width="5" transform="rotate(-200 70 70)"/><circle cx="70" cy="70" r="54" fill="#fff"/><g fill="none" stroke="#f26522" stroke-width="2"><path d="M44 90h52M48 90V70h44v20M54 70V56h14v14M72 56h16v14M76 48h8v8M56 78h6M66 78h6M76 78h6M86 78h2M56 84h32"/></g></svg>
    <h3>Construction And<br>Engineering</h3>
  </div>
  <div class="service" style="left:691px;top:185px">
    <svg width="140" height="140" viewBox="0 0 140 140"><path d="M70 2a68 68 0 1 1-68 68" fill="none" stroke="#1e8fe8" stroke-width="5" transform="rotate(-200 70 70)"/><circle cx="70" cy="70" r="54" fill="#fff"/><g fill="none" stroke="#222" stroke-width="2.5"><path d="M70 46l20 7v15c0 13-9 20-20 24-11-4-20-11-20-24V53z"/><path d="M66 60h8v7h7v8h-7v7h-8v-7h-7v-8h7z"/></g></svg>
    <h3>Casualty Workmen ’s<br>Compensation Health Insurance</h3>
  </div>
  <div class="service" style="left:887px;top:185px">
    <svg width="140" height="140" viewBox="0 0 140 140"><path d="M70 2a68 68 0 1 1-68 68" fill="none" stroke="#1e8fe8" stroke-width="5" transform="rotate(-200 70 70)"/><circle cx="70" cy="70" r="54" fill="#fff"/><g fill="none" stroke="#222" stroke-width="2"><rect x="44" y="52" width="52" height="26"/><circle cx="70" cy="65" r="7"/><path d="M48 65h10M82 65h10"/><circle cx="56" cy="86" r="5" fill="#222"/><circle cx="84" cy="86" r="5" fill="#222"/></g></svg>
    <h3>Marime And Transit<br>Credit</h3>
  </div>
</section>

<!-- testimonial -->
<section class="testimonial" role="img" aria-label="Hands cupping a row of wooden blocks under a dark overlay">
  <div class="eyebrow" style="top:64px">Testimonial</div>
  <h2 class="title" style="top:84px">What Our Clients Say</h2>
  <div class="title-rule" style="top:124px"></div>
  <p class="lead" style="top:130px">Lorem ipsum dolor sit amet, consectetuer adipiscing elit, sed diam nonummy nibh euismod tincidunt ut laoreet dolore magna</p>
  <div class="avatar" role="img" aria-label="Client portrait"></div>
  <div class="client-name">Clients Name</div>
  <div class="client-role">- Designer</div>
  <p class="quote">Lorem ipsum dolor sit amet, consectetuer adipiscing elit, sed diam nonummy nibh euismod tincidunt ut laoreet dolore magna aliquam erat volutpat. Ut wisi enim ad minim veniam, quis nostrud exerci tation ullamcorper suscipit lobortis nisl ut aliquip ex ea commodo consequat. Duis autem vel eum iriure dolor in hendrerit in vulputate velit esse molestie consequat, vel illum dolore eu feugiat nulla facilisis at vero eros et accumsan et iusto odio dignissim qui blandit augue duis dolore te feugait nulla facilisi.</p>
  <div class="dots"><span></span><span class="on"></span><span></span></div>
</section>

<!-- team -->
<div class="eyebrow" style="top:2133px">Our Team</div>
<h2 class="title" style="top:2152px">Lantern insurance Team</h2>
<div class="title-rule" style="top:2192px"></div>
<p class="lead" style="top:2207px">Lorem ipsum dolor sit amet, consectetuer adipiscing elit, sed diam nonummy nibh euismod tincidunt ut laoreet dolore magna</p>

<article class="member" style="left:143px"><div class="photo" role="img" aria-label="Senior manager in a navy suit, arms crossed"></div><h3>Your Name</h3><div class="role">General Manager</div><p>Lorem ipsum dolor sit amet, rtetuer adipiscinger elit werr werr veniam werwerr erewer.</p></article>
<article class="member" style="left:377px"><div class="photo" role="img" aria-label="Young manager in a dark suit and tie"></div><div class="social-strip"><span></span><span></span><span></span></div><h3>Your Name</h3><div class="role">General Manager</div><p>Lorem ipsum dolor sit amet, rtetuer adipiscinger elit werr werr veniam werwerr erewer.</p></article>
<article class="member" style="left:612px"><div class="photo" role="img" aria-label="Manager in a suit standing before office buildings"></div><h3>Your Name</h3><div class="role">General Manager</div><p>Lorem ipsum dolor sit amet, rtetuer adipiscinger elit werr werr veniam werwerr erewer.</p></article>
<article class="member" style="left:846px"><div class="photo" role="img" aria-label="Smiling manager in a black suit pointing"></div><h3>Your Name</h3><div class="role">General Manager</div><p>Lorem ipsum dolor sit amet, rtetuer adipiscinger elit werr werr veniam werwerr erewer.</p></article>

<!-- contact -->
<section class="contact">
  <div class="eyebrow" style="top:73px">Get in Touch</div>
  <h2 class="title" style="top:96px">Contact Us</h2>
  <div class="title-rule" style="top:136px"></div>
  <p class="lead" style="top:150px">Lorem ipsum dolor sit amet, consectetuer adipiscing elit, sed diam nonummy nibh euismod tincidunt ut laoreet dolore magna</p>
  <div class="field" style="left:143px;top:190px;width:450px">First Name*</div>
  <div class="field" style="left:609px;top:190px;width:450px">Last Name*</div>
  <div class="field" style="left:143px;top:242px;width:450px">Email*</div>
  <div class="field" style="left:609px;top:242px;width:450px">Company Name*</div>
  <div class="field" style="left:143px;top:295px;width:450px">Your Tittle*</div>
  <div class="field" style="left:609px;top:295px;width:450px">Phone*</div>
  <div class="field message" style="left:143px;top:348px;width:913px">Message*</div>
  <a class="btn" style="left:546px;top:474px;width:124px">SUBMIT</a>
</section>

<!-- newsletter -->
<section class="newsletter">
  <div class="nl-icon"><svg width="16" height="12" viewBox="0 0 16 12"><rect x="1" y="1" width="14" height="10" fill="none" stroke="#fff" stroke-width="1.5"/><path d="M1 1l7 6 7-6" fill="none" stroke="#fff" stroke-width="1.5"/></svg></div>
  <div class="nl-title">Newsletter Signup</div>
  <svg class="abs" style="left:438px;top:14px" width="24" height="42" viewBox="0 0 24 42"><path d="M3 2l18 19L3 40" fill="none" stroke="#fff" stroke-width="1.5"/></svg>
  <div class="nl-input">Your e-mail</div>
  <div class="nl-btn">SIGN UP</div>
</section>

<!-- footer -->
<footer class="site-footer">
  <div class="foot-title" style="left:143px;top:36px">QUICK LINK</div>
  <div class="foot-rule" style="left:143px;top:68px;width:190px"></div>
  <ul class="quick-links">
    <li class="active">HOME</li><li>WHO WE ARE</li><li>WHAT WE DO</li><li>TESTIMONIAL</li><li>OUR TEAM</li><li>CONTACT US</li>
  </ul>
  <div class="vline"></div>
  <div class="foot-title" style="left:413px;top:36px">GET IN TOUCH</div>
  <div class="foot-rule" style="left:413px;top:68px;width:200px"></div>
  <div class="info" style="top:85px"><span class="ico"><svg width="10" height="14" viewBox="0 0 10 14"><path d="M5 0a5 5 0 0 1 5 5c0 4-5 9-5 9S0 9 0 5a5 5 0 0 1 5-5z" fill="#fff"/><circle cx="5" cy="5" r="2" fill="#1e8fe8"/></svg></span><div><strong>Lantern Insurance</strong>Lorem Ipsum Dolor Sit Amet,<br>Adipiscinger Elit Werr.</div></div>
  <div class="info" style="top:167px;align-items:center"><span class="ico"><svg width="12" height="12" viewBox="0 0 24 24"><path fill="#fff" d="M6.6 10.8a15 15 0 0 0 6.6 6.6l2.2-2.2c.3-.3.7-.4 1-.2 1.1.4 2.3.6 3.6.6.6 0 1 .4 1 1V20c0 .6-.4 1-1 1A17 17 0 0 1 3 4c0-.6.4-1 1-1h3.5c.6 0 1 .4 1 1 0 1.3.2 2.5.6 3.6.1.3 0 .7-.2 1z"/></svg></span>+123 555 0148</div>
  <div class="info" style="top:224px;align-items:center"><span class="ico"><svg width="12" height="9" viewBox="0 0 16 12"><rect x="1" y="1" width="14" height="10" fill="none" stroke="#fff" stroke-width="1.8"/><path d="M1 1l7 6 7-6" fill="none" stroke="#fff" stroke-width="1.8"/></svg></span>info@lanterninsurance.com</div>
  <div class="social"><span></span><span></span><span></span></div>
  <div class="map" role="img" aria-label="Street map of the office district with a red location pin"></div>
</footer>
<div class="copyright">Copyright 2019 Lantern Insurance Brokers. All Rights Reserved.</div>

</body>
</html>
```